Construction Company

Design a clutter free business card, it can be double-sided utilizing the logo for VKM Ltd simple with all relevant contact information.

Please also a letterhead design to function for the purposes of invoicing, all mail requirements, with header to be distinctive while the footer ties page together and incorporates all necessary information.

For now, please use generic / dummy text and when a winner is selected, I will disclose the contact information.

Hi Designers! Please read the updated brief which includes the design of a business card and letterhead. Thank you!

```html
<!DOCTYPE html>
<html lang="en">
<head>
<meta charset="utf-8">
<title>VKM Ltd – Business Card</title>
<link rel="stylesheet" href="https://fonts.googleapis.com/css2?family=Libre+Baskerville:wght@700&family=Arimo:wght@400&display=swap">
<style>
  :root {
    --royal-blue: #0a2f9c;
    --gold: #c49a22;
    --white: #ffffff;
    --ink: #2a2a2a;
    --rule: #9a9a9a;
    --backdrop: #e6e7eb;
  }
  * { box-sizing: border-box; margin: 0; padding: 0; }
  html, body { width: 1200px; height: 866px; overflow: hidden; }
  body {
    background: var(--backdrop);
    display: flex;
    flex-direction: column;
    align-items: center;
    justify-content: center;
    gap: 56px;
    font-family: "Arimo", Arial, sans-serif;
  }
  .card {
    position: relative;
    width: 580px;
    height: 331px;
    box-shadow: 0 6px 18px rgba(0,0,0,.18);
  }
  .card--front { background: var(--white); }
  .card--back {
    background: var(--royal-blue);
    display: flex;
    align-items: center;
    justify-content: center;
  }

  .wordmark {
    display: flex;
    align-items: center;
    gap: 12px;
    font-family: "Libre Baskerville", Georgia, serif;
    font-weight: 700;
    letter-spacing: 1px;
    white-space: nowrap;
  }
  .wordmark__dot {
    border-radius: 50%;
    background: var(--gold);
    flex: none;
  }
  .wordmark--front {
    position: absolute;
    right: 46px;
    top: 92px;
    font-size: 44px;
    color: var(--royal-blue);
  }
  .wordmark--front .wordmark__dot { width: 22px; height: 22px; }
  .wordmark--back { font-size: 60px; color: var(--white); }
  .wordmark--back .wordmark__dot { width: 28px; height: 28px; }

  .holder {
    position: absolute;
    left: 38px;
    top: 40px;
  }
  .holder__name {
    font-family: "Libre Baskerville", Georgia, serif;
    font-weight: 700;
    font-size: 17px;
    letter-spacing: 1.5px;
    color: var(--royal-blue);
    text-transform: uppercase;
  }
  .holder__title {
    margin-top: 4px;
    font-size: 13px;
    color: var(--ink);
  }
  .contact-list {
    list-style: none;
    margin-top: 12px;
    font-size: 12.5px;
    color: var(--ink);
    line-height: 19px;
  }
  .contact-list li { display: flex; align-items: center; gap: 8px; }
  .contact-list svg { width: 12px; height: 12px; flex: none; fill: var(--royal-blue); }
  .contact-list .web-host { color: var(--royal-blue); }

  .divider {
    position: absolute;
    left: 200px;
    right: 40px;
    top: 222px;
    height: 1px;
    background: var(--rule);
  }
  .address {
    position: absolute;
    right: 40px;
    top: 240px;
    font-size: 13px;
    line-height: 19px;
    color: var(--ink);
    text-align: right;
  }
</style>
</head>
<body>

  <section class="card card--front" aria-label="Business card front">
    <div class="holder">
      <p class="holder__name">Daniel Harper</p>
      <p class="holder__title">Managing Director</p>
      <ul class="contact-list">
        <li>
          <svg viewBox="0 0 12 12" aria-hidden="true"><path d="M2.5 1l2 2.4-1 1.2c.6 1.4 1.6 2.4 3 3l1.2-1 2.4 2-1 1.9C5.2 10.4 1.6 6.8 1 2z"/></svg>
          044-987 654 321
        </li>
        <li>
          <svg viewBox="0 0 12 12" aria-hidden="true"><path d="M3 0h6v12H3zM4 1.5v8h4v-8z"/></svg>
          044-987 654 321
        </li>
        <li>
          <svg viewBox="0 0 12 12" aria-hidden="true"><path d="M0 2h12v8H0zM1 3l5 3.5L11 3z"/></svg>
          info@vkmbuild.com
        </li>
        <li>
          <svg viewBox="0 0 12 12" aria-hidden="true"><path d="M6 0a6 6 0 1 0 0 12A6 6 0 0 0 6 0zm0 1c.8 0 1.6 2 1.7 4.5H4.3C4.4 3 5.2 1 6 1zM1 6.5h2.3c.1 1.7.5 3.2 1.1 4.2A5 5 0 0 1 1 6.5zm0-1A5 5 0 0 1 4.4 1.3C3.8 2.3 3.4 3.8 3.3 5.5zm3.3 1h3.4C7.6 9 6.8 11 6 11s-1.6-2-1.7-4.5zm4.4 0H11a5 5 0 0 1-3.4 4.2c.6-1 1-2.5 1.1-4.2zm0-1c-.1-1.7-.5-3.2-1.1-4.2A5 5 0 0 1 11 5.5z"/></svg>
          www.<span class="web-host">vkmbuild</span>.com
        </li>
      </ul>
    </div>

    <div class="wordmark wordmark--front">
      <span class="wordmark__dot" aria-hidden="true"></span>
      <span>VKM LTD</span>
    </div>

    <div class="divider" aria-hidden="true"></div>

    <p class="address">421, Address line goes here<br>45452, Country Name</p>
  </section>

  <section class="card card--back" aria-label="Business card back">
    <div class="wordmark wordmark--back">
      <span class="wordmark__dot" aria-hidden="true"></span>
      <span>VKM LTD</span>
    </div>
  </section>

</body>
</html>
```